Essential Oil 15ml - package of 6

Design of a box of 6 different essential oils.
+ design of the bottle stickers
My bottles are 15ml clear blue glass.

The pictures attached are my competitors...

Target Market(s)

TERVIK USA

Font styles to use
Serif

Requirements
Must have
• Our logo + "essential oil" and type (lavender, eucalyptus etc....)
• 15ml - 0.50 fl.oz.
• special color for the oil type.

```html
<!DOCTYPE html>
<html lang="en">
<head>
<meta charset="utf-8">
<title>Sela Vale Essential Oil Labels</title>
<link rel="stylesheet" href="https://fonts.googleapis.com/css2?family=Libre+Caslon+Text&family=Source+Sans+3:wght@300;600&display=swap">
<style>
  :root {
    --sheet: #b0b1b5;
    --gold-text: #e9a650;
    --gold-light: #f6d38e;
    --bronze: #8c4f1f;
    --rust: #7c3518;
    --band-ink: #2a2016;
    --eucalyptus-a: #1f3446; --eucalyptus-b: #40708f; --eucalyptus-c: #25455d;
    --teatree-a: #3a3e26; --teatree-b: #5f6e45; --teatree-c: #363722;
    --lavender-a: #3c3048; --lavender-b: #433651; --lavender-c: #2f2533;
    --peppermint-a: #1f3524; --peppermint-b: #3a7a5a; --peppermint-c: #243e2b;
    --rosemary-a: #3e141c; --rosemary-b: #6d2631; --rosemary-c: #35121a;
    --orange-a: #a2301a; --orange-b: #e26325; --orange-c: #701c12;
  }
  * { margin: 0; padding: 0; box-sizing: border-box; }
  html, body { width: 1200px; height: 1200px; overflow: hidden; }
  body { background: var(--sheet); position: relative; }

  .label {
    position: absolute; height: 216px; overflow: hidden;
  }
  .label-inner {
    position: absolute; left: 0; top: 0; width: 657px; height: 216px;
    text-align: center;
  }
  .brand-dot {
    position: absolute; left: 306px; top: 12px;
    width: 52px; height: 52px; border-radius: 50%;
    background: var(--gold-text);
  }
  .brand-name {
    position: absolute; left: 0; right: 0; top: 70px;
    font: 600 29px/1 "Source Sans 3", sans-serif;
    color: var(--gold-text);
  }
  .oil-band {
    position: absolute; left: 0; top: 107px; width: 100%; height: 35px;
    background: linear-gradient(90deg, var(--bronze) 0%, #c98e4f 15%, var(--gold-light) 30%, #e9be78 55%, var(--bronze) 75%, var(--rust) 100%);
  }
  .oil-name {
    position: absolute; left: 0; right: 0; top: 111px;
    font: 400 25px/1 "Libre Caslon Text", serif;
    letter-spacing: 1px; color: var(--band-ink);
  }
  .product-type {
    position: absolute; left: 0; right: 0; top: 162px;
    font: 300 19px/1 "Source Sans 3", sans-serif;
    color: var(--gold-text);
  }
  .volume {
    position: absolute; left: 0; right: 0; top: 192px;
    font: 300 13px/1 "Source Sans 3", sans-serif;
    color: var(--gold-text);
  }

  .eucalyptus { left: 3px; top: 14px; width: 657px;
    background: linear-gradient(90deg, var(--eucalyptus-a), var(--eucalyptus-b) 20%, var(--eucalyptus-c) 45%, var(--eucalyptus-c) 80%, var(--eucalyptus-a)); }
  .tea-tree { left: 660px; top: 14px; width: 540px;
    background: linear-gradient(90deg, var(--teatree-a), var(--teatree-a) 45%, var(--teatree-b) 75%, var(--teatree-c)); }
  .lavender { left: 3px; top: 234px; width: 657px;
    background: linear-gradient(90deg, var(--lavender-a), var(--lavender-b) 50%, var(--lavender-c)); }
  .peppermint { left: 3px; top: 454px; width: 657px;
    background: linear-gradient(90deg, var(--peppermint-a), var(--peppermint-c) 25%, var(--peppermint-b) 55%, var(--peppermint-b) 80%, var(--peppermint-a)); }
  .rosemary { left: 3px; top: 671px; width: 657px;
    background: linear-gradient(90deg, var(--rosemary-a), var(--rosemary-b) 45%, var(--rosemary-b) 75%, var(--rosemary-c)); }
  .sweet-orange { left: 3px; top: 890px; width: 657px;
    background: linear-gradient(90deg, var(--orange-a), var(--orange-b) 45%, var(--orange-b) 80%, var(--orange-c)); }
  .sweet-orange .oil-name { color: #5a2410; }
</style>
</head>
<body>
  <section class="label eucalyptus"><div class="label-inner">
    <span class="brand-dot"></span><div class="brand-name">Sela Vale</div>
    <div class="oil-band"></div><div class="oil-name">EUCALYPTUS</div>
    <div class="product-type">PureEssential Oil</div><div class="volume">15ml (0.50 fl.oz)</div>
  </div></section>

  <section class="label tea-tree"><div class="label-inner">
    <span class="brand-dot"></span><div class="brand-name">Sela Vale</div>
    <div class="oil-band"></div><div class="oil-name">TEA TREE</div>
    <div class="product-type">PureEssential Oil</div><div class="volume">15ml (0.50 fl.oz)</div>
  </div></section>

  <section class="label lavender"><div class="label-inner">
    <span class="brand-dot"></span><div class="brand-name">Sela Vale</div>
    <div class="oil-band"></div><div class="oil-name">LAVENDER</div>
    <div class="product-type">PureEssential Oil</div><div class="volume">15ml (0.50 fl.oz)</div>
  </div></section>

  <section class="label peppermint"><div class="label-inner">
    <span class="brand-dot"></span><div class="brand-name">Sela Vale</div>
    <div class="oil-band"></div><div class="oil-name">PEPPERMINT</div>
    <div class="product-type">PureEssential Oil</div><div class="volume">15ml (0.50 fl.oz)</div>
  </div></section>

  <section class="label rosemary"><div class="label-inner">
    <span class="brand-dot"></span><div class="brand-name">Sela Vale</div>
    <div class="oil-band"></div><div class="oil-name">ROSEMARY</div>
    <div class="product-type">PureEssential Oil</div><div class="volume">15ml (0.50 fl.oz)</div>
  </div></section>

  <section class="label sweet-orange"><div class="label-inner">
    <span class="brand-dot"></span><div class="brand-name">Sela Vale</div>
    <div class="oil-band"></div><div class="oil-name">SWEET ORANGE</div>
    <div class="product-type">PureEssential Oil</div><div class="volume">15ml (0.50 fl.oz)</div>
  </div></section>
</body>
</html>
```